Business Card Update, need to bring life to the card, two sided color

We need a new business card design, are moving and changing addresses and need a new look, we have the logos already attached but need a new style moving forward. Can incorporate the color of the logo (The Green) as well, maybe a solid back? We deal with safety products revolving around static electricity and safety lighting. Would like to keep same font in second logo as well.

Target Market(s)

Electrical Safety, Lighting

Contact Information for Business Card

Dale Fenwick
Vice President
Office: 770-555-4821
Cell: 770-555-3067
dale@tkfenwick.example
www.tkfenwick.example
4700 West Harbor Boulevard
Suite #150
Roswell, GA 30076

Font styles to use
Serif
Sans Serif

Requirements
Must have
• Since 1918
Nice to have
• Could use the 100 Year Logo for back of card, would like the back of card to be the same green as logo.
Should not have
• No black cards please.

```html
<!DOCTYPE html>
<html lang="en">
<head>
<meta charset="utf-8">
<title>T.K. Fenwick Business Card</title>
<link href="https://fonts.googleapis.com/css2?family=Arimo:wght@700&family=Source+Sans+3:wght@400;600&display=swap" rel="stylesheet">
<style>
  :root {
    --green: #00965a;
    --black: #000000;
    --ink: #1a1a1a;
    --white: #ffffff;
    --stage: #eef3f1;
    --frame: #222222;
  }
  * { margin: 0; padding: 0; box-sizing: border-box; }
  html, body { width: 1200px; height: 1008px; overflow: hidden; }
  body {
    position: relative;
    background: var(--stage);
    border: 3px solid var(--frame);
    font-family: "Source Sans 3", Arial, sans-serif;
  }
  .card { position: absolute; overflow: hidden; }

  /* Front */
  .card-front {
    left: 65px; top: 32px; width: 766px; height: 437px;
    border-radius: 12px; border: 1.5px solid var(--black);
    background: var(--white);
  }
  .card-front .swoosh { position: absolute; inset: 0; width: 100%; height: 100%; }
  .brand-mark {
    position: absolute; left: 286px; top: 26px;
    width: 112px; height: 112px; border-radius: 50%;
    background: var(--green);
  }
  .brand-front {
    position: absolute; left: 410px; top: 52px;
    font-family: "Arimo", Arial, sans-serif; font-weight: 700;
    color: var(--green); text-align: center;
  }
  .brand-front .brand-name { font-size: 34px; line-height: 40px; }
  .brand-front .brand-sub { font-size: 17px; line-height: 20px; }
  .contact-list { position: absolute; left: 21px; top: 252px; list-style: none; color: var(--white); font-size: 19px; }
  .contact-list li { display: flex; align-items: center; height: 33px; }
  .contact-list svg { width: 17px; height: 17px; margin-right: 6px; flex: none; }
  .holder { position: absolute; right: 35px; top: 262px; text-align: right; color: var(--white); }
  .holder-name { font-family: "Arimo", Arial, sans-serif; font-weight: 700; font-size: 29px; line-height: 36px; }
  .holder-title { font-family: "Arimo", Arial, sans-serif; font-weight: 700; font-size: 22px; line-height: 28px; margin-top: 4px; }
  .holder-address { font-size: 19px; line-height: 24px; margin-top: 10px; }

  /* Back */
  .card-back {
    left: 294px; top: 498px; width: 828px; height: 473px;
    border-radius: 43px; background: var(--green);
    text-align: center;
  }
  .back-mark {
    position: absolute; left: 300px; top: 29px;
    width: 228px; height: 228px; border-radius: 50%;
    background: var(--black);
  }
  .brand-back {
    position: absolute; left: 0; right: 0; top: 270px;
    font-family: "Arimo", Arial, sans-serif; font-weight: 700; color: var(--black);
  }
  .brand-back .brand-name { font-size: 44px; line-height: 50px; }
  .brand-back .brand-sub { font-size: 20px; line-height: 24px; }
  .brand-back .since { font-family: "Source Sans 3", Arial, sans-serif; font-weight: 600; font-size: 20px; line-height: 24px; margin-top: 14px; letter-spacing: 0.12em; }
  .back-web {
    position: absolute; left: 0; right: 0; top: 424px;
    font-size: 27px; letter-spacing: 0.24em; color: var(--ink);
  }
</style>
</head>
<body>
  <section class="card card-front">
    <svg class="swoosh" viewBox="0 0 896 511" preserveAspectRatio="none" aria-hidden="true">
      <defs>
        <linearGradient id="silver" x1="0" y1="0" x2="1" y2="0">
          <stop offset="0" stop-color="#9a9b9d"/>
          <stop offset="0.6" stop-color="#ffffff"/>
          <stop offset="1" stop-color="#c8c8c8"/>
        </linearGradient>
        <linearGradient id="silver-low" x1="0" y1="1" x2="1" y2="0">
          <stop offset="0" stop-color="#9a9b9d"/>
          <stop offset="0.5" stop-color="#f4f4f4"/>
          <stop offset="1" stop-color="#d8d8d8"/>
        </linearGradient>
      </defs>
      <path d="M0,185 C300,270 600,268 896,243 L896,511 L0,511 Z" fill="var(--green)"/>
      <path d="M0,152 C300,245 600,262 896,243 C600,272 300,272 0,185 Z" fill="url(#silver)"/>
      <path d="M0,0 L28,0 C200,150 500,245 896,243 C600,262 300,248 0,152 Z" fill="var(--black)"/>
      <path d="M210,511 C400,380 650,280 896,243 L896,511 Z" fill="url(#silver-low)"/>
      <path d="M305,511 C480,390 700,290 896,243 L896,511 Z" fill="var(--black)"/>
    </svg>

    <div class="brand-mark"></div>
    <div class="brand-front">
      <div class="brand-name">T.K. Fenwick</div>
      <div class="brand-sub">Manufacturing Company, Inc.</div>
    </div>

    <ul class="contact-list">
      <li>
        <svg viewBox="0 0 20 20" aria-hidden="true"><circle cx="10" cy="10" r="8.5" fill="none" stroke="#fff" stroke-width="1.6"/><path d="M7 5.5 L8.6 8 L7.6 9 C8.3 10.6 9.4 11.7 11 12.4 L12 11.4 L14.5 13 L13.5 14.6 C9.5 14.5 5.5 10.5 5.4 6.5 Z" fill="#fff"/></svg>
        Office: 770-555-4821
      </li>
      <li>
        <svg viewBox="0 0 20 20" aria-hidden="true"><circle cx="10" cy="10" r="8.5" fill="none" stroke="#fff" stroke-width="1.6"/><rect x="7" y="4.5" width="6" height="11" rx="1" fill="none" stroke="#fff" stroke-width="1.4"/><circle cx="10" cy="13.2" r="0.8" fill="#fff"/></svg>
        Cell: 770-555-3067
      </li>
      <li>
        <svg viewBox="0 0 20 20" aria-hidden="true"><circle cx="10" cy="10" r="8.5" fill="none" stroke="#fff" stroke-width="1.6"/><rect x="5.5" y="7" width="9" height="6.5" fill="none" stroke="#fff" stroke-width="1.4"/><path d="M5.5 7 L10 10.5 L14.5 7" fill="none" stroke="#fff" stroke-width="1.4"/></svg>
        dale@tkfenwick.example
      </li>
      <li>
        <svg viewBox="0 0 20 20" aria-hidden="true"><g fill="none" stroke="#fff" stroke-width="1.4"><circle cx="10" cy="10" r="8"/><ellipse cx="10" cy="10" rx="3.5" ry="8"/><path d="M2 10 H18 M3.5 6 H16.5 M3.5 14 H16.5"/></g></svg>
        www.tkfenwick.example
      </li>
    </ul>

    <div class="holder">
      <div class="holder-name">Dale Fenwick</div>
      <div class="holder-title">Vice President</div>
      <div class="holder-address">4700 West Harbor Boulevard<br>Suite #150<br>Roswell, GA 30076</div>
    </div>
  </section>

  <section class="card card-back">
    <div class="back-mark"></div>
    <div class="brand-back">
      <div class="brand-name">T.K. Fenwick</div>
      <div class="brand-sub">Manufacturing Company, Inc.</div>
      <div class="since">Since 1918</div>
    </div>
    <div class="back-web">www.tkfenwick.example</div>
  </section>
</body>
</html>
```